Detail Shop Business card design

i need a business card design for my new detailing company called 'Brisk's Polish Works'. i want an all black and white design . simple, direct and to the point. i want the designer to choose a fitting font to match the logothe front should have logo, address, phone and email and the back side should have a slogan and text indicating that we offer services on anything including cars, trucks, motorcycles and RVs. slogan will read "we take pride in your ride"
maybe also very small on the back side the IG icon with Brisks_Polish_Works

phone 208.417.6352
address 3847 E Larkin Ave
Spokane WA 99214
email: BrisksPolish@mailvexo.com

Target Market(s)

all ages , auto enthusiasts

Industry/Entity Type

Automotive

Contact Information for Business Card

the front should have logo, address, phone and email and the back side should have a slogan and text indicating that we offer services on anything including cars, trucks, motorcycles and RVs. slogan will read "we take pride in your ride"

phone 208.417.6352
address 3847 E Larkin Ave
Spokane WA 99214

Colors
000000
ffffff

Requirements
Must have
• bold font and very simple design with good spacing
Nice to have
• anything creative from the designer indicating we service any types of vehicles
Should not have
• any colors ,

```html
<!DOCTYPE html>
<html lang="en">
<head>
<meta charset="utf-8">
<title>Brisk's Polish Works – Business Card</title>
<link rel="stylesheet" href="https://fonts.googleapis.com/css2?family=Oswald:wght@500;700&family=Roboto+Condensed:wght@400;700&display=swap">
<style>
  :root {
    --ink: #111111;
    --soft-ink: #555555;
    --paper: #ffffff;
    --back-card: #555555;
    --back-text: #1a1a1a;
    --stage: #e9e9e9;
  }
  * { box-sizing: border-box; margin: 0; padding: 0; }
  html, body { width: 1200px; height: 950px; overflow: hidden; }
  body {
    background: var(--stage);
    font-family: "Roboto Condensed", Arial, sans-serif;
    display: flex;
    flex-direction: column;
    align-items: center;
    justify-content: center;
    gap: 60px;
  }
  .card {
    position: relative;
    width: 630px;
    height: 360px;
    box-shadow: 0 6px 18px rgba(0,0,0,0.18);
    overflow: hidden;
  }

  /* Front */
  .card-front { background: var(--paper); color: var(--ink); }
  .divider {
    position: absolute;
    left: 330px; top: 0;
    width: 2px; height: 120px;
    background: var(--ink);
  }
  .brand {
    position: absolute;
    left: 40px; top: 120px;
    width: 250px;
    display: flex;
    align-items: center;
    gap: 14px;
  }
  .brand-dot {
    flex: none;
    width: 44px; height: 44px;
    border-radius: 50%;
    background: var(--ink);
  }
  .brand-name {
    font-family: "Oswald", Impact, sans-serif;
    font-weight: 700;
    font-size: 30px;
    line-height: 1.05;
    text-transform: uppercase;
    color: var(--ink);
  }
  .details {
    position: absolute;
    left: 360px; top: 130px;
    width: 250px;
  }
  .person-name {
    display: flex; align-items: center; gap: 8px;
    font-weight: 700; font-size: 22px; letter-spacing: 0.5px;
  }
  .person-name svg { width: 14px; height: 14px; }
  .person-role {
    margin-left: 22px;
    font-size: 16px; color: var(--soft-ink);
  }
  .rule {
    margin: 14px 0 14px 22px;
    width: 190px; height: 2px; background: var(--ink);
  }
  .contact-list { list-style: none; }
  .contact-list li {
    display: flex; align-items: flex-start; gap: 10px;
    font-size: 14.5px; line-height: 19px; color: var(--soft-ink);
  }
  .contact-list svg { flex: none; width: 12px; height: 12px; margin-top: 4px; }
  .contact-list .group { margin-bottom: 8px; }

  /* Back */
  .card-back { background: var(--back-card); color: var(--back-text); }
  .vehicle-art {
    position: absolute;
    left: 150px; top: 30px;
    width: 400px; height: 200px;
    border-radius: 90px 110px 40px 40px;
    background: linear-gradient(180deg, #1d1d1d 0%, #0a0a0a 100%);
  }
  .slogan-block {
    position: absolute;
    left: 40px; right: 40px; bottom: 40px;
  }
  .slogan {
    font-family: "Oswald", Impact, sans-serif;
    font-weight: 700; font-size: 24px;
    letter-spacing: 1px; text-transform: uppercase;
  }
  .slogan-rule { margin: 6px 0 8px; width: 340px; height: 2px; background: var(--back-text); }
  .services {
    font-family: "Oswald", Impact, sans-serif;
    font-weight: 500; font-size: 16px;
  }
</style>
</head>
<body>
  <section class="card card-front" aria-label="Business card front">
    <div class="divider"></div>
    <div class="brand">
      <span class="brand-dot"></span>
      <span class="brand-name">Brisk's Polish Works</span>
    </div>
    <div class="details">
      <div class="person-name">
        <svg viewBox="0 0 14 14" aria-hidden="true"><circle cx="7" cy="4" r="3.5" fill="#111"/><path d="M0 14c0-4 3-6 7-6s7 2 7 6z" fill="#111"/></svg>
        DALE MORGAN
      </div>
      <div class="person-role">CEO/FOUNDER</div>
      <div class="rule"></div>
      <ul class="contact-list">
        <li class="group">
          <svg viewBox="0 0 12 12" aria-hidden="true"><path d="M6 0a4 4 0 0 0-4 4c0 3 4 8 4 8s4-5 4-8a4 4 0 0 0-4-4z" fill="#111"/><circle cx="6" cy="4" r="1.5" fill="#fff"/></svg>
          <span>3847 E Larkin Ave<br>Spokane WA 99214</span>
        </li>
        <li>
          <svg viewBox="0 0 12 12" aria-hidden="true"><path d="M2 0l3 3-1.5 1.5c.8 1.6 2 2.8 3.6 3.6L8.5 6.6l3 3L10 12C5 11 1 7 0 2z" fill="#111"/></svg>
          <span>208.417.6352</span>
        </li>
        <li class="group">
          <svg viewBox="0 0 12 12" aria-hidden="true"><rect x="2.5" y="0.5" width="7" height="11" rx="1" fill="none" stroke="#111"/><circle cx="6" cy="9.5" r="0.8" fill="#111"/></svg>
          <span>208 552 7140</span>
        </li>
        <li>
          <svg viewBox="0 0 12 12" aria-hidden="true"><rect x="0" y="2" width="12" height="8" fill="#111"/><path d="M0 2l6 5 6-5" fill="none" stroke="#fff"/></svg>
          <span>BrisksPolish@mailvexo.com</span>
        </li>
        <li>
          <svg viewBox="0 0 12 12" aria-hidden="true"><circle cx="6" cy="6" r="5.5" fill="#111"/><path d="M0.5 6h11M6 0.5c-3 3-3 8 0 11M6 0.5c3 3 3 8 0 11" fill="none" stroke="#fff" stroke-width="0.8"/></svg>
          <span>www.briskspolish.com</span>
        </li>
      </ul>
    </div>
  </section>

  <section class="card card-back" aria-label="Business card back">
    <div class="vehicle-art" role="img" aria-label="Black silhouette illustration of a classic hot rod car"></div>
    <div class="slogan-block">
      <p class="slogan">We take pride in your ride</p>
      <div class="slogan-rule"></div>
      <p class="services">We offer services on anything including cars, trucks, motorcycles &amp; RVs</p>
    </div>
  </section>
</body>
</html>
```